Real Estate Webpage Design

We have an existing website: ferndaleestatecollective.com.au
We focus customised service mainly on Property Management and second-hand property sales.
We are not entirely happy about the current design and layout can stay roughly the same as the back end coding is linked to a CRM system.
We would like to see the design are more reachable to our clients and appearing.
Please check our Website Design Draft for more details.

Industry/Entity Type

Real estate Agency

Number of Pages Required

5+ page

Font styles to use
Sans Serif

Colors

Designer to choose colors to be used in the design.

```html
<!DOCTYPE html>
<html lang="en">
<head>
<meta charset="utf-8">
<title>Ferndale Estate Collective</title>
<link href="https://fonts.googleapis.com/css2?family=Poppins:wght@400;500;600&display=swap" rel="stylesheet">
<style>
:root{
  --gold:#ecbd57;
  --navy:#14264a;
  --footer:#13233f;
  --text:#1b2a45;
  --muted:#7d8190;
  --cream:#fdfcf8;
  --white:#ffffff;
}
*{margin:0;padding:0;box-sizing:border-box}
html,body{width:675px;height:1200px;overflow:hidden;background:var(--white)}
body{font-family:'Poppins',sans-serif;color:var(--text);position:relative}
.abs{position:absolute}
/* hero */
.hero{left:0;top:0;width:675px;height:232px;background:linear-gradient(100deg,#f4f4f3 0%,#e9e9e7 45%,#d8d8d6 70%,#bdbdbb 100%)}
.hero-sofa{left:365px;top:170px;width:310px;height:62px;background:linear-gradient(180deg,#5a5a5a,#3a3a3a);border-radius:8px 0 0 0}
.brand{left:34px;top:10px;display:flex;align-items:center;gap:6px}
.brand-mark{width:30px;height:30px;border:3px solid var(--gold)}
.brand-name{font-size:22px;font-weight:500;color:var(--gold);line-height:1}
.brand-sub{font-size:6px;letter-spacing:1px;color:var(--text);margin-top:2px}
.nav{left:245px;top:14px;display:flex;gap:14px;font-size:8px;color:var(--text)}
.btn-gold{background:var(--gold);color:var(--white);font-size:7.5px;display:flex;align-items:center;justify-content:center;border-left:1.5px solid #c9962f}
.nav-cta{left:570px;top:11px;width:71px;height:19px}
.hero-title{left:34px;top:74px;width:340px;font-size:21px;font-weight:600;line-height:27px;color:var(--navy)}
.hero-title span{color:var(--gold)}
.hero-sub{left:34px;top:136px;font-size:7.5px;color:var(--text)}
.hero-cta{left:34px;top:167px;width:84px;height:19px}
/* features */
.card{width:103px;height:91px;background:var(--white);box-shadow:0 0 8px rgba(0,0,0,.06);display:flex;flex-direction:column;align-items:center;justify-content:center;text-align:center;font-size:9.5px;font-weight:500;color:var(--navy);line-height:13px;gap:6px}
.eyebrow{left:287px;top:283px;font-size:7.5px;color:var(--gold)}
.h2{font-size:15px;font-weight:600;color:var(--navy)}
.body{font-size:7.5px;line-height:12.6px;color:var(--muted)}
/* promise */
.promise{left:0;top:544px;width:675px;height:294px;background:var(--cream)}
.house{left:363px;top:581px;width:278px;height:221px;background:linear-gradient(180deg,#cfd2d6 0%,#e8e8e6 45%,#d9d5cf 75%,#6f8a4d 100%)}
.strong{font-size:7.5px;font-weight:500;color:var(--navy)}
/* cta band */
.band{left:0;top:878px;width:675px;height:127px;background:var(--gold)}
.band-title{left:150px;top:904px;width:390px;text-align:center;font-size:13px;font-weight:600;line-height:19px;color:var(--white)}
.band-btn{left:279px;top:956px;width:117px;height:20px;background:var(--navy);color:var(--white);font-size:7.5px;display:flex;align-items:center;justify-content:center}
/* footer */
.footer{left:0;top:1005px;width:675px;height:195px;background:var(--footer)}
.foot-brand .brand-name{color:var(--white);font-size:22px}
.foot-brand .brand-mark{border-color:var(--white)}
.foot-brand .brand-sub{color:var(--white)}
.foot-h{font-size:8px;font-weight:600;color:var(--gold)}
.foot-text{font-size:7px;line-height:12.5px;color:var(--white)}
.links{list-style:none;font-size:7px;color:var(--white)}
.links li{height:15.1px;display:flex;align-items:center;gap:4px}
.social{width:22px;height:22px;border-radius:50%;border:1px solid var(--white)}
.social.on{background:var(--gold);border-color:var(--gold)}
.legal{left:0;top:1179px;width:675px;height:21px;border-top:1px solid #2a3a58;display:flex;align-items:center;padding:0 34px;font-size:7px;color:var(--white)}
.legal .links-row{margin-left:auto;display:flex;gap:12px}
</style>
</head>
<body>

<div class="abs hero" role="img" aria-label="Bright white living room interior with shelves, plants and a dark sofa"></div>
<div class="abs hero-sofa" role="img" aria-label="Dark grey sofa"></div>

<div class="abs brand">
  <div class="brand-mark"></div>
  <div><div class="brand-name">Ferndale</div><div class="brand-sub">PropertyGroup</div></div>
</div>
<nav class="abs nav">
  <span>Home</span><span>About Us</span><span>Leasing</span><span>Buy</span><span>Sell</span><span>Our Team</span><span>Blog</span><span>Contact Us</span>
</nav>
<div class="abs btn-gold nav-cta">Add Properties</div>

<h1 class="abs hero-title">Welcome To <span>Ferndale</span> Property Group</h1>
<p class="abs hero-sub">Your local real estate property group</p>
<div class="abs btn-gold hero-cta">See All Properties</div>

<!-- features -->
<div class="abs card" style="left:34px;top:279px">
  <svg width="30" height="30" viewBox="0 0 30 30" fill="none" stroke="#14264a" stroke-width="1.2"><rect x="3" y="2" width="19" height="26" rx="1"/><circle cx="12" cy="8" r="2.5"/><path d="M7 21h11M7 24h11M7 18h11"/><circle cx="23" cy="9" r="4" stroke="#ecbd57"/></svg>
  Great Experience
</div>
<div class="abs card" style="left:149px;top:279px">
  <svg width="30" height="30" viewBox="0 0 30 30" fill="none" stroke="#14264a" stroke-width="1.2"><rect x="10" y="2" width="10" height="9" stroke="#ecbd57"/><path d="M1 14h5v10H1M29 14h-5v10h5M6 16l6-3 4 2 4-2 4 3M8 22l4 3 3-2 3 2 6-5"/></svg>
  Safety Deals
</div>
<div class="abs card" style="left:34px;top:379px">
  <svg width="30" height="30" viewBox="0 0 30 30" fill="none" stroke="#14264a" stroke-width="1.2"><circle cx="14" cy="13" r="5"/><path d="M5 26c1-5 5-7 9-7s8 2 9 7"/><path d="M5 14a9 9 0 0 1 16-6" stroke="#ecbd57"/><rect x="21" y="2" width="7" height="5" stroke="#ecbd57"/></svg>
  Comprehensive<br>Support
</div>
<div class="abs card" style="left:149px;top:379px">
  <svg width="30" height="30" viewBox="0 0 30 30" fill="none" stroke="#14264a" stroke-width="1.2"><circle cx="9" cy="8" r="5"/><rect x="17" y="6" width="8" height="10" stroke="#ecbd57"/><path d="M2 18h4v10H2M6 20h8l8-2c3-1 4 2 2 3l-9 5H6"/></svg>
  Property<br>Management
</div>

<p class="abs eyebrow">About Us</p>
<h2 class="abs h2" style="left:287px;top:296px">Who Is Ferndale?</h2>
<p class="abs body" style="left:287px;top:319px;width:350px">Ferndale stands for the home, the house; buying a property is one of the most expensive expenses and important assets for people. Ferndale is a real estate company located in Marrowby, Canberra.</p>
<p class="abs body" style="left:287px;top:362px;width:350px">Being a portfolio sales agent and property manager, coupled with our high-profile international real estate experience, Ferndale is considered a market leader on the cutting edge with deep industry knowledge, ranging from landlord-tenant relationships, residential purchases.</p>
<h2 class="abs h2" style="left:286px;top:426px">What do we do?</h2>
<p class="abs body" style="left:286px;top:449px;width:358px">Helping landlords and vendor alike to complete efficient property transactions is our signature talent. Our poise, precision, and insight give us an unparalleled advantage. Beyond the core real estate services, we engender trust and cultivate relationships, an approach that generates repeat business from a high-quality client base.</p>

<!-- promise -->
<div class="abs promise"></div>
<h2 class="abs h2" style="left:34px;top:572px">Our Promise:</h2>
<p class="abs body" style="left:34px;top:592px;width:305px">Ferndale Estate Collective aims to at all times maintain the utmost levels of service for our customers and strives to place itself at the forefront of Property Management Services within the Real Estate industry.</p>
<h2 class="abs h2" style="left:34px;top:650px">Why choose us?</h2>
<p class="abs strong" style="left:34px;top:671px">We care people, we value service.</p>
<p class="abs body" style="left:34px;top:682px;width:305px">Since we connect people to their homes and to their communities. Relationships are everything to us. Our clients' needs and best interests are at the heart of everything we do.</p>
<h2 class="abs h2" style="left:34px;top:735px;width:230px;line-height:21px">Work with us and see the potential</h2>
<p class="abs body" style="left:34px;top:777px;width:305px">We are here to guide you into your dream property and will always enjoy being part of your first step to completing that project you've always dreamed of.</p>
<div class="abs house" role="img" aria-label="Modern white two-storey family house with dark roof and timber accent"></div>

<!-- cta -->
<div class="abs band"></div>
<h2 class="abs band-title">Contact Us If You Want To Sell Your House Or You Have Other Questions</h2>
<div class="abs band-btn">Request Free Consultation</div>

<!-- footer -->
<footer class="abs footer"></footer>
<div class="abs brand foot-brand" style="top:1032px">
  <div class="brand-mark"></div>
  <div><div class="brand-name">Ferndale</div><div class="brand-sub">PropertyGroup</div></div>
</div>
<p class="abs foot-text" style="left:34px;top:1070px;width:125px">Lorem ipsum dolor sit amet, consectetur adipiscing elit, sed do eiusmod tempor...</p>

<h3 class="abs foot-h" style="left:185px;top:1030px">Site Map</h3>
<ul class="abs links" style="left:184px;top:1050px">
  <li>⟶ Home</li><li>⟶ About Us</li><li>⟶ Leasing</li><li>⟶ Buy</li><li>⟶ Sell</li><li>⟶ Our Team</li><li>⟶ Blog</li><li>⟶ Contact Us</li>
</ul>

<h3 class="abs foot-h" style="left:345px;top:1030px">Contact Us</h3>
<svg class="abs" style="left:344px;top:1053px" width="11" height="12" viewBox="0 0 11 12" fill="none" stroke="#fff" stroke-width=".8"><path d="M5.5 11S1.5 7 1.5 4.5a4 4 0 0 1 8 0C9.5 7 5.5 11 5.5 11z"/><circle cx="5.5" cy="4.5" r="1.5"/></svg>
<p class="abs foot-text" style="left:362px;top:1053px;width:130px;font-size:6.8px;line-height:11px">18/4 Wattlebird Lane, Marrowby , ACT, 2900</p>
<svg class="abs" style="left:344px;top:1080px" width="11" height="11" viewBox="0 0 11 11" fill="none" stroke="#fff" stroke-width=".8"><path d="M2 1l2 2-1 1.5c.8 1.6 2 2.8 3.5 3.5L8 7l2 2-1.5 1.5C4.5 10 1 6.5.5 2.5z"/></svg>
<p class="abs foot-text" style="left:364px;top:1078px;font-weight:600;line-height:13px">02 5550 1847<br>02 5550 6203</p>
<svg class="abs" style="left:344px;top:1110px" width="12" height="9" viewBox="0 0 12 9" fill="none" stroke="#fff" stroke-width=".8"><rect x=".5" y=".5" width="11" height="8"/><path d="M.5.5l5.5 4.5L11.5.5"/></svg>
<p class="abs foot-text" style="left:362px;top:1107px">hello@ferndaleestate.com.au</p>

<h3 class="abs foot-h" style="left:500px;top:1030px">Follow On Us</h3>
<div class="abs social on" style="left:499px;top:1053px"></div>
<div class="abs social" style="left:530px;top:1053px"></div>
<div class="abs social" style="left:561px;top:1053px"></div>
<div class="abs social" style="left:591px;top:1053px"></div>

<div class="abs legal">
  <span>2022© Ferndale Estate Collective. All right reserved.</span>
  <span class="links-row"><span>Privacy</span><span>Complaint Handling &amp; Dispute Resolution</span><span>Due Diligence Checklist</span></span>
</div>

</body>
</html>
```